Bramblewood Card Company Business Cards

We are a trading card store with Glimmorax, sports and other TCG cards, we need a business card design that encompasses a clean cut, modern style with a retro flare. website is bramblewoodcardco.com for reference. Can utilize a comic book era feel or a more modern outdoor feel to utilize the "Pacific Northwest" elements of tress, mountains, etc.

Industry/Entity Type

Trading cards and collectibles

Contact Information for Business Card

business name, email address, phone number, name, owner job title

Font styles to use
Sans Serif

```html
<!DOCTYPE html>
<html lang="en">
<head>
<meta charset="utf-8">
<title>Bramblewood Card Company – Business Cards</title>
<link href="https://fonts.googleapis.com/css2?family=Arimo:wght@400;700&display=swap" rel="stylesheet">
<style>
  :root {
    --stage: #2b2b2b;
    --card-dark: #1f1f1f;
    --card-light: #ffffff;
    --brand-cyan: #17b6d9;
    --brand-grey: #6e6e6e;
    --text-grey: #6a6a6a;
    --rule-grey: #555555;
  }
  * { box-sizing: border-box; margin: 0; padding: 0; }
  html, body {
    width: 1200px;
    height: 900px;
    overflow: hidden;
    background: var(--stage);
    font-family: "Arimo", Arial, sans-serif;
  }
  .sheet {
    width: 1200px;
    height: 900px;
    display: flex;
    flex-direction: column;
    align-items: center;
    justify-content: center;
    gap: 40px;
  }
  .card {
    width: 700px;
    height: 400px;
    border-radius: 22px;
    position: relative;
    display: flex;
    flex-direction: column;
    align-items: center;
    box-shadow: 0 10px 24px rgba(0, 0, 0, 0.35);
  }
  .card--front {
    background: var(--card-dark);
    justify-content: center;
  }
  .card--back {
    background: var(--card-light);
    padding-top: 70px;
  }
  .brand {
    display: flex;
    align-items: center;
    gap: 18px;
  }
  .brand__mark {
    width: 58px;
    height: 58px;
    background: var(--brand-cyan);
    border-radius: 6px;
    flex: none;
  }
  .brand__name {
    font-weight: 700;
    font-size: 34px;
    letter-spacing: 3px;
    text-transform: uppercase;
    line-height: 1.15;
    color: var(--brand-grey);
  }
  .card--front .brand__name { color: var(--card-light); }
  .brand__name span { display: block; }
  .contact-row {
    position: absolute;
    left: 0;
    right: 0;
    bottom: 72px;
    display: flex;
    justify-content: center;
    align-items: center;
    gap: 20px;
    padding-right: 40px;
  }
  .person { text-align: right; }
  .person__name {
    font-weight: 700;
    font-size: 28px;
    color: var(--brand-cyan);
    text-transform: uppercase;
    line-height: 1.1;
  }
  .person__title {
    font-size: 22px;
    color: var(--text-grey);
    line-height: 1.2;
  }
  .divider {
    width: 2px;
    height: 58px;
    background: var(--rule-grey);
  }
  .contact-list { list-style: none; }
  .contact-list li {
    display: flex;
    align-items: center;
    gap: 12px;
    font-size: 22px;
    color: var(--text-grey);
    line-height: 1.4;
  }
  .contact-list svg { width: 20px; height: 20px; flex: none; }
</style>
</head>
<body>
  <main class="sheet">
    <section class="card card--front" aria-label="Card front">
      <div class="brand">
        <span class="brand__mark" aria-hidden="true"></span>
        <p class="brand__name"><span>Bramblewood</span><span>Card Company</span></p>
      </div>
    </section>

    <section class="card card--back" aria-label="Card back">
      <div class="brand">
        <span class="brand__mark" aria-hidden="true"></span>
        <p class="brand__name"><span>Bramblewood</span><span>Card Company</span></p>
      </div>

      <div class="contact-row">
        <div class="person">
          <p class="person__name">Marcus Hale</p>
          <p class="person__title">Manager</p>
        </div>
        <div class="divider"></div>
        <ul class="contact-list">
          <li>
            <svg viewBox="0 0 24 24" fill="none" stroke="var(--brand-cyan)" stroke-width="2" stroke-linecap="round" stroke-linejoin="round" aria-hidden="true">
              <path d="M5 3h3l2 5-2.5 1.5a11 11 0 0 0 7 7L16 14l5 2v3a2 2 0 0 1-2 2A16 16 0 0 1 3 5a2 2 0 0 1 2-2z"/>
            </svg>
            360-555-0148
          </li>
          <li>
            <svg viewBox="0 0 24 24" fill="none" stroke="var(--brand-cyan)" stroke-width="2" stroke-linejoin="round" aria-hidden="true">
              <rect x="2.5" y="5" width="19" height="14" rx="1.5"/>
              <path d="M3 6l9 7 9-7"/>
            </svg>
            info@bramblewoodcardco.com
          </li>
        </ul>
      </div>
    </section>
  </main>
</body>
</html>
```